Brightmill Data Works

Our company is about IT hardwares and IT solutions. IT hardware such as PC, RAMS, storage and servers. IT solutions such as project management, BA. We are also selling new technology too.

Target Market(s)

Consumer, Small to Medium Business, Corporate

Requirements
Must have
• The business card must have the following:
• Name:
• Title:
• Contact Number:
• Email address:
• Website:
• Color: Must match the logo color upgrade

```html
<!DOCTYPE html>
<html lang="en">
<head>
<meta charset="utf-8">
<title>Brightmill Data Works — Business Card</title>
<link href="https://fonts.googleapis.com/css2?family=Saira:wght@300;400;700&display=swap" rel="stylesheet">
<style>
  :root {
    --bg: #2b2b2b;
    --orange: #b8611f;
    --orange-light: #cf8a2e;
    --ink: #3a3a3a;
    --card: #f1f1f1;
    --card-back: #dcdcdc;
  }
  * { box-sizing: border-box; margin: 0; padding: 0; }
  html, body {
    width: 1200px; height: 923px; overflow: hidden;
    background: var(--bg);
    font-family: "Saira", sans-serif;
  }
  .stage {
    width: 1200px; height: 923px;
    display: flex; flex-direction: column;
    align-items: center; justify-content: center; gap: 44px;
  }
  .card {
    position: relative;
    width: 620px; height: 354px;
    overflow: hidden;
  }
  /* Back side */
  .card--back {
    background: var(--card-back);
    border: 20px solid var(--orange);
    display: flex; align-items: center; justify-content: center;
  }
  .brand {
    display: flex; align-items: center; gap: 12px;
  }
  .brand__mark {
    width: 22px; height: 22px; background: var(--orange);
  }
  .brand__name {
    font-weight: 700; color: var(--ink);
    text-transform: uppercase; letter-spacing: 0.5px;
    line-height: 1.05;
  }
  .card--back .brand__name { font-size: 30px; }

  /* Front side */
  .card--front { background: var(--card); }
  .card__band {
    position: absolute; left: 0; right: 0; bottom: 0;
    height: 46px; background: var(--orange);
  }
  .card__brand {
    position: absolute; left: 0; top: 0; width: 300px; height: 308px;
    display: flex; align-items: center; justify-content: center;
  }
  .card__brand .brand { flex-direction: column; gap: 14px; }
  .card__brand .brand__mark { width: 34px; height: 34px; }
  .card__brand .brand__name { font-size: 30px; text-align: center; }
  .card__divider {
    position: absolute; left: 300px; top: 48px;
    width: 3px; height: 214px; background: var(--orange);
  }
  .card__details {
    position: absolute; left: 330px; top: 56px; right: 20px;
  }
  .person__name {
    font-weight: 400; font-size: 24px; color: var(--ink);
    text-transform: uppercase; line-height: 1;
  }
  .person__title {
    font-weight: 400; font-size: 19px; color: var(--orange-light);
    text-transform: uppercase; line-height: 1.1; margin-top: 2px;
  }
  .contacts { list-style: none; margin-top: 58px; }
  .contact {
    display: flex; align-items: center; gap: 10px;
    font-weight: 300; font-size: 18px; color: #222;
    margin-bottom: 10px; line-height: 1;
  }
  .contact__icon { width: 22px; height: 22px; flex: none; }
</style>
</head>
<body>
<main class="stage">
  <section class="card card--back" aria-label="Card back">
    <div class="brand">
      <span class="brand__mark"></span>
      <span class="brand__name">Brightmill Data Works</span>
    </div>
  </section>

  <section class="card card--front" aria-label="Card front">
    <div class="card__brand">
      <div class="brand">
        <span class="brand__mark"></span>
        <span class="brand__name">Brightmill<br>Data Works</span>
      </div>
    </div>
    <div class="card__divider"></div>
    <div class="card__details">
      <p class="person__name">Aiden Marlow</p>
      <p class="person__title">Manager</p>
      <ul class="contacts">
        <li class="contact">
          <svg class="contact__icon" viewBox="0 0 22 22" aria-hidden="true">
            <rect width="22" height="22" fill="#b8611f"/>
            <path d="M7 5 L9.5 5 L10.5 8 L9 9.2 C9.8 11 11 12.2 12.8 13 L14 11.5 L17 12.5 L17 15 C17 16 16 17 15 17 C10 16.5 5.5 12 5 7 C5 6 6 5 7 5 Z" fill="#fff"/>
          </svg>
          +1-555-014-2387
        </li>
        <li class="contact">
          <svg class="contact__icon" viewBox="0 0 22 22" aria-hidden="true">
            <rect width="22" height="22" fill="#b8611f"/>
            <rect x="4.5" y="6.5" width="13" height="9" fill="none" stroke="#fff" stroke-width="1.4"/>
            <path d="M4.5 6.5 L11 12 L17.5 6.5" fill="none" stroke="#fff" stroke-width="1.4"/>
          </svg>
          aiden@brightmilldata.com
        </li>
        <li class="contact">
          <svg class="contact__icon" viewBox="0 0 22 22" aria-hidden="true">
            <rect width="22" height="22" fill="#b8611f"/>
            <circle cx="11" cy="11" r="6.5" fill="none" stroke="#fff" stroke-width="1.3"/>
            <ellipse cx="11" cy="11" rx="2.8" ry="6.5" fill="none" stroke="#fff" stroke-width="1.1"/>
            <path d="M4.5 11 H17.5 M5.5 8 H16.5 M5.5 14 H16.5" stroke="#fff" stroke-width="1"/>
          </svg>
          www.brightmilldata.com
        </li>
      </ul>
    </div>
    <div class="card__band"></div>
  </section>
</main>
</body>
</html>
```